Business Card Design

I give lessons and clinics for dressage riders
I would like the design to be an outline (with broad lines) of a dressage horse and rider with in background of whole card with print over top tan or parchment card with burgundy print

Industry/Entity Type

Business

Contact Information for Business Card

Dale Ferrin
612-374-2059
Classical dressage training for the modern American
Clinics, lessons, training level -Prix St. George

Requirements
Must have
• broad lined outline of dressage horse and rider

```html
<!DOCTYPE html>
<html lang="en">
<head>
<meta charset="UTF-8">
<title>Dale Ferrin – Business Card</title>
<link href="https://fonts.googleapis.com/css2?family=Arimo:wght@400&display=swap" rel="stylesheet">
<style>
  :root {
    --page-bg: #e4e4e6;
    --card-white: #ffffff;
    --band-black: #050505;
    --panel-brown: #4a3018;
    --figure-tan: #b5a596;
    --text-light: #ffffff;
  }
  html, body {
    margin: 0;
    padding: 0;
    width: 1200px;
    height: 864px;
    overflow: hidden;
    background: var(--page-bg);
  }
  .card {
    position: absolute;
    left: 75px;
    top: 132px;
    width: 1050px;
    height: 600px;
    background: var(--card-white);
    box-shadow: 0 6px 24px rgba(0, 0, 0, 0.18);
    overflow: hidden;
    font-family: "Arimo", Arial, sans-serif;
  }
  .card-art {
    position: absolute;
    inset: 0;
    width: 100%;
    height: 100%;
  }
  .contact {
    position: absolute;
    right: 62px;
    top: 228px;
    text-align: right;
    color: var(--text-light);
  }
  .contact-name {
    margin: 0;
    font-size: 35px;
    font-weight: 400;
    letter-spacing: 0.5px;
    text-transform: uppercase;
  }
  .contact-phone {
    margin: 4px 0 0;
    font-size: 19px;
  }
  .tagline {
    margin: 42px 0 0;
    font-size: 22px;
    line-height: 31px;
  }
</style>
</head>
<body>
  <div class="card">
    <svg class="card-art" viewBox="0 0 1050 600" xmlns="http://www.w3.org/2000/svg">
      <path class="band-black" fill="var(--band-black)"
            d="M975 0 C800 260 450 470 0 480 L0 600 L60 600 C450 500 850 300 995 0 Z"/>
      <path class="panel-brown" fill="var(--panel-brown)"
            d="M995 0 C850 300 450 500 60 600 L1050 600 L1050 0 Z"/>
      <path class="rider-figure" role="img" aria-label="Broad-lined outline of a dressage horse and rider"
            fill="var(--figure-tan)" opacity="0.85"
            d="M40 120 Q120 70 210 95 Q300 110 380 140 Q420 200 400 300 Q360 360 300 380 Q200 420 120 440 Q60 445 40 420 Z"/>
    </svg>
    <div class="contact">
      <h1 class="contact-name">Dale Ferrin</h1>
      <p class="contact-phone">612-374-2059</p>
      <p class="tagline">Classical dressage training for the<br>modern American Clinics<br>lessons, training level, Prix St. George</p>
    </div>
  </div>
</body>
</html>
```